female esthetician looking for an impact business card

I an an expert in skin care industry with high experience in NYC.I want my business card to look professional , an impact at first look. I do want a combination between white and gold . I believe the font will be great if is gold.. The Fonts are also important. MIRABELA COSTINA (SKIN CARE BOUTIQUE)

THIS SHOULD BE THE BUSINESS NAME, and should be placed on th eback of the card.
IN front m, the name MIRABELA COSTINA - ESTHETCIAN

BY APPOINTMENTS ONLY: 518.240.7136

Target Market(s)

HIGH END CLIENTELE

Contact Information for Business Card

iT WILL BE on a luxury paper. I neeed the wow feeling

Requirements
Should not have
• pictures

```html
<!DOCTYPE html>
<html lang="en">
<head>
<meta charset="UTF-8">
<title>Mirabela Costina – Skin Care Boutique Business Card</title>
<link rel="stylesheet" href="https://fonts.googleapis.com/css2?family=Jost:wght@400;500&display=swap">
<style>
  :root {
    --backdrop: #1b1b1b;
    --card-black: #1e1e1e;
    --gold-light: #f6e88a;
    --gold-mid: #d9b23a;
    --gold-deep: #b8871f;
    --gold-text: #c99a2e;
    --ink: #1a1a1a;
  }
  * { margin: 0; padding: 0; box-sizing: border-box; }
  html, body {
    width: 1200px;
    height: 895px;
    overflow: hidden;
    background: var(--backdrop);
    font-family: "Jost", "Futura", sans-serif;
  }
  .canvas {
    position: relative;
    width: 1200px;
    height: 895px;
  }
  .card {
    position: absolute;
    left: 320px;
    width: 560px;
    height: 320px;
    box-shadow: 0 14px 30px rgba(0, 0, 0, 0.55);
  }

  /* Front: gold face with business name */
  .card-front {
    top: 95px;
    background: linear-gradient(100deg,
      var(--gold-deep) 0%,
      var(--gold-mid) 18%,
      var(--gold-light) 38%,
      var(--gold-mid) 55%,
      var(--gold-light) 72%,
      var(--gold-mid) 88%,
      var(--gold-deep) 100%);
  }
  .brand-name {
    position: absolute;
    top: 118px;
    left: 0;
    width: 100%;
    text-align: center;
    font-size: 34px;
    font-weight: 400;
    letter-spacing: 6px;
    color: var(--ink);
  }
  .brand-tagline {
    position: absolute;
    top: 196px;
    left: 0;
    width: 100%;
    text-align: center;
    font-size: 15px;
    font-weight: 400;
    letter-spacing: 2.5px;
    color: var(--ink);
  }

  /* Back: black face with contact details */
  .card-back {
    top: 480px;
    background: var(--card-black);
  }
  .person {
    position: absolute;
    top: 138px;
    left: 72px;
    text-align: right;
    color: var(--gold-text);
  }
  .person-name {
    font-size: 21px;
    font-weight: 400;
    letter-spacing: 0.5px;
  }
  .person-title {
    font-size: 17px;
    font-weight: 400;
    margin-top: -2px;
  }
  .divider {
    position: absolute;
    top: 132px;
    left: 298px;
    width: 1px;
    height: 44px;
    background: var(--gold-text);
  }
  .contact {
    position: absolute;
    top: 134px;
    left: 318px;
    color: var(--gold-text);
    font-size: 16px;
    font-weight: 400;
  }
  .contact-phone {
    display: flex;
    align-items: center;
    gap: 7px;
    margin-top: 2px;
    padding-left: 18px;
  }
  .contact-phone svg { width: 13px; height: 13px; fill: var(--gold-text); }
  .gold-rule {
    position: absolute;
    left: 0;
    right: 0;
    bottom: 18px;
    height: 4px;
    background: linear-gradient(90deg, var(--gold-deep), var(--gold-light), var(--gold-mid));
  }
</style>
</head>
<body>
  <main class="canvas">
    <section class="card card-front">
      <h1 class="brand-name">MIRABELA COSTINA</h1>
      <p class="brand-tagline">SKIN CARE BOUTIQUE</p>
    </section>

    <section class="card card-back">
      <div class="person">
        <h2 class="person-name">MIRABELA COSTINA</h2>
        <p class="person-title">Esthetcian</p>
      </div>
      <span class="divider"></span>
      <div class="contact">
        <p class="contact-note">By appointments only:</p>
        <p class="contact-phone">
          <svg viewBox="0 0 24 24" aria-hidden="true"><path d="M6.6 10.8a15.1 15.1 0 0 0 6.6 6.6l2.2-2.2a1 1 0 0 1 1-.25 11.4 11.4 0 0 0 3.6.57 1 1 0 0 1 1 1V20a1 1 0 0 1-1 1A17 17 0 0 1 3 4a1 1 0 0 1 1-1h3.5a1 1 0 0 1 1 1c0 1.25.2 2.45.57 3.57a1 1 0 0 1-.25 1z"/></svg>
          <span>518.240.7136</span>
        </p>
      </div>
      <span class="gold-rule"></span>
    </section>
  </main>
</body>
</html>
```